Brookmere Osteopathy flyer

I want a clean clear DL flyer (but also want an A4 poster) promoting a new Osteopathic business in a semi rural area in Tasmania (Australia).
It can have pictures like the examples attached to show people what Osteopathy is (its like Chiropractic and physiotherapy).
I am the sole practioner and am male, so any pictures would be best to be a white male if possible.
I've attached some wording, you can use all, or none of it
I don't have a phone number for the business yet
info@brookmereosteopathy.example
www.brookmereosteopathy.example
Target Market(s)
Australians, from tradies, professionals, babies to retired people
Industry/Entity Type
Health
Look and feel

```html
<!DOCTYPE html>
<html lang="en">
<head>
<meta charset="utf-8">
<title>Brookmere Osteopathy Flyer</title>
<link href="https://fonts.googleapis.com/css2?family=Montserrat:wght@400;500;600;700&family=Open+Sans:wght@700&family=Poppins:wght@300;500;600&display=swap" rel="stylesheet">
<style>
  :root {
    --backdrop: #404040;
    --cream: #fdf5f1;
    --blue: #1e9ad6;
    --orange: #f0964a;
    --ink: #111111;
    --body: #1c1c1c;
  }
  * { margin: 0; padding: 0; box-sizing: border-box; }
  html, body { width: 897px; height: 1200px; overflow: hidden; background: var(--backdrop); }
  .canvas { position: relative; width: 897px; height: 1200px; }
  .flyer {
    position: absolute; left: 103px; top: 113px; width: 691px; height: 974px;
    background: var(--cream);
  }
  .shapes { position: absolute; left: 0; top: 0; width: 897px; height: 1200px; }
  .abs { position: absolute; white-space: nowrap; line-height: 1; }

  .brand { left: 143px; top: 216px; display: flex; align-items: center; gap: 10px;
    font-family: "Poppins", sans-serif; font-weight: 500; font-size: 16px; color: var(--blue); }
  .brand-dot { width: 26px; height: 26px; border: 2px solid var(--blue); border-radius: 50%; }

  .title-top { left: 141px; top: 318px; font-family: "Montserrat", sans-serif; font-weight: 400;
    font-size: 54px; letter-spacing: -1.5px; color: var(--blue); }
  .title-main { left: 141px; top: 366px; font-family: "Montserrat", sans-serif; font-weight: 700;
    font-size: 52px; letter-spacing: -2px; color: var(--orange); }
  .tagline { left: 143px; top: 423px; font-family: "Open Sans", sans-serif; font-weight: 700;
    font-size: 26px; letter-spacing: -0.5px; color: var(--ink); }

  .section-head { font-family: "Poppins", sans-serif; font-weight: 600; font-size: 30px; letter-spacing: -1.5px; }
  .reasons-a { left: 142px; top: 487px; color: var(--blue); }
  .reasons-b { left: 142px; top: 516px; color: var(--orange); }

  .reasons-list { position: absolute; left: 141px; top: 568px; list-style: none;
    font-family: "Poppins", sans-serif; font-weight: 300; font-size: 17px; color: var(--ink); }
  .reasons-list li { display: flex; align-items: center; height: 24.4px; gap: 7px; white-space: nowrap; }
  .tick { width: 16px; height: 16px; flex: none; }

  .about { position: absolute; left: 142px; top: 833px; width: 496px;
    font-family: "Montserrat", sans-serif; font-weight: 500; font-size: 12px; line-height: 14.2px;
    text-align: justify; color: var(--body); }

  .contact-head { left: 142px; top: 946px; color: var(--blue); }
  .contact-list { position: absolute; left: 141px; top: 991px; list-style: none;
    font-family: "Montserrat", sans-serif; font-weight: 600; font-size: 13px; color: var(--ink); }
  .contact-list li { display: flex; align-items: center; gap: 8px; height: 18.5px; white-space: nowrap; }
  .contact-icon { width: 13px; height: 13px; flex: none; }
</style>
</head>
<body>
<div class="canvas">
  <div class="flyer"></div>

  <svg class="shapes" viewBox="0 0 897 1200" xmlns="http://www.w3.org/2000/svg">
    <defs>
      <linearGradient id="treatment-tones" x1="0" y1="0" x2="1" y2="1">
        <stop offset="0" stop-color="#c98068"/>
        <stop offset="0.45" stop-color="#e9d7cc"/>
        <stop offset="1" stop-color="#b47a5c"/>
      </linearGradient>
      <linearGradient id="neck-tones" x1="0" y1="0" x2="1" y2="1">
        <stop offset="0" stop-color="#e9e7e6"/>
        <stop offset="0.55" stop-color="#c99478"/>
        <stop offset="1" stop-color="#efeceb"/>
      </linearGradient>
    </defs>

    <path class="band-orange" fill="var(--orange)"
      d="M677,432 Q700,452 735,440 L794,422 V1087 H590 Q660,900 686,672 Z"/>
    <path class="band-blue" fill="var(--blue)"
      d="M794,722 V1087 H617 Q720,920 794,722 Z"/>

    <path class="photo-frame" fill="var(--cream)" stroke="var(--cream)" stroke-width="18" stroke-linejoin="round"
      d="M650,444 L756,505 L756,621 L650,682 L544,621 L544,505 Z"/>

    <path role="img" aria-label="Photo: osteopath working on a patient's upper back in a brick-walled treatment room"
      fill="url(#treatment-tones)"
      d="M525,113 H794 V396 L735,423 Q724,429 712,423 L545,333 Q525,322 525,300 Z"/>

    <path role="img" aria-label="Photo: patient lying on a treatment table while the practitioner supports his neck"
      fill="url(#neck-tones)" stroke="url(#neck-tones)" stroke-width="10" stroke-linejoin="round"
      d="M650,463 L739,514 L739,612 L650,663 L561,612 L561,514 Z"/>
  </svg>

  <div class="abs brand"><span class="brand-dot"></span>Brookmere Osteopathy</div>

  <div class="abs title-top">BROOKMERE</div>
  <div class="abs title-main">OSTEOPATHY</div>
  <div class="abs tagline">MOVE BETTER, FEEL BETTER</div>

  <div class="abs section-head reasons-a">COMMON REASONS</div>
  <div class="abs section-head reasons-b">PEOPLE VISIT AN OSTEOPATH</div>

  <ul class="reasons-list">
    <li><svg class="tick" viewBox="0 0 16 16"><path d="M13.5,7.2 A6,6 0 1 1 10.5,2.6" fill="none" stroke="var(--orange)" stroke-width="1.8" stroke-linecap="round"/><path d="M4.8,7.6 L7.6,10.2 L14.3,3.2" fill="none" stroke="var(--orange)" stroke-width="1.8" stroke-linecap="round" stroke-linejoin="round"/></svg>Sciatica</li>
    <li><svg class="tick" viewBox="0 0 16 16"><path d="M13.5,7.2 A6,6 0 1 1 10.5,2.6" fill="none" stroke="var(--orange)" stroke-width="1.8" stroke-linecap="round"/><path d="M4.8,7.6 L7.6,10.2 L14.3,3.2" fill="none" stroke="var(--orange)" stroke-width="1.8" stroke-linecap="round" stroke-linejoin="round"/></svg>Plantar fasciitis</li>
    <li><svg class="tick" viewBox="0 0 16 16"><path d="M13.5,7.2 A6,6 0 1 1 10.5,2.6" fill="none" stroke="var(--orange)" stroke-width="1.8" stroke-linecap="round"/><path d="M4.8,7.6 L7.6,10.2 L14.3,3.2" fill="none" stroke="var(--orange)" stroke-width="1.8" stroke-linecap="round" stroke-linejoin="round"/></svg>Tendonitis / Bursitis</li>
    <li><svg class="tick" viewBox="0 0 16 16"><path d="M13.5,7.2 A6,6 0 1 1 10.5,2.6" fill="none" stroke="var(--orange)" stroke-width="1.8" stroke-linecap="round"/><path d="M4.8,7.6 L7.6,10.2 L14.3,3.2" fill="none" stroke="var(--orange)" stroke-width="1.8" stroke-linecap="round" stroke-linejoin="round"/></svg>Adhesive capsulitis (frozen shoulder)</li>
    <li><svg class="tick" viewBox="0 0 16 16"><path d="M13.5,7.2 A6,6 0 1 1 10.5,2.6" fill="none" stroke="var(--orange)" stroke-width="1.8" stroke-linecap="round"/><path d="M4.8,7.6 L7.6,10.2 L14.3,3.2" fill="none" stroke="var(--orange)" stroke-width="1.8" stroke-linecap="round" stroke-linejoin="round"/></svg>Tennis / Golfers elbow</li>
    <li><svg class="tick" viewBox="0 0 16 16"><path d="M13.5,7.2 A6,6 0 1 1 10.5,2.6" fill="none" stroke="var(--orange)" stroke-width="1.8" stroke-linecap="round"/><path d="M4.8,7.6 L7.6,10.2 L14.3,3.2" fill="none" stroke="var(--orange)" stroke-width="1.8" stroke-linecap="round" stroke-linejoin="round"/></svg>Back / neck pain</li>
    <li><svg class="tick" viewBox="0 0 16 16"><path d="M13.5,7.2 A6,6 0 1 1 10.5,2.6" fill="none" stroke="var(--orange)" stroke-width="1.8" stroke-linecap="round"/><path d="M4.8,7.6 L7.6,10.2 L14.3,3.2" fill="none" stroke="var(--orange)" stroke-width="1.8" stroke-linecap="round" stroke-linejoin="round"/></svg>Headaches / migraines</li>
    <li><svg class="tick" viewBox="0 0 16 16"><path d="M13.5,7.2 A6,6 0 1 1 10.5,2.6" fill="none" stroke="var(--orange)" stroke-width="1.8" stroke-linecap="round"/><path d="M4.8,7.6 L7.6,10.2 L14.3,3.2" fill="none" stroke="var(--orange)" stroke-width="1.8" stroke-linecap="round" stroke-linejoin="round"/></svg>Joint and muscle pain</li>
    <li><svg class="tick" viewBox="0 0 16 16"><path d="M13.5,7.2 A6,6 0 1 1 10.5,2.6" fill="none" stroke="var(--orange)" stroke-width="1.8" stroke-linecap="round"/><path d="M4.8,7.6 L7.6,10.2 L14.3,3.2" fill="none" stroke="var(--orange)" stroke-width="1.8" stroke-linecap="round" stroke-linejoin="round"/></svg>Pregnancy-related discomfort</li>
    <li><svg class="tick" viewBox="0 0 16 16"><path d="M13.5,7.2 A6,6 0 1 1 10.5,2.6" fill="none" stroke="var(--orange)" stroke-width="1.8" stroke-linecap="round"/><path d="M4.8,7.6 L7.6,10.2 L14.3,3.2" fill="none" stroke="var(--orange)" stroke-width="1.8" stroke-linecap="round" stroke-linejoin="round"/></svg>Disc related issues</li>
  </ul>

  <p class="about">Brookmere Osteopathy use a tailored combination of joint mobilisation/manipulation, stretching, movement, trigger point dry needling and targeted massage to reduce pain and restore optimal function. Hands-on treatment is backed up with rehabilitative exercise prescription and advice. So whether you're recovering from injury or managing chronic discomfort, we’re here to help you move better and feel your best.</p>

  <div class="abs section-head contact-head">CONTACT US</div>
  <ul class="contact-list">
    <li><svg class="contact-icon" viewBox="0 0 14 14"><path d="M7,13 C7,13 2.5,8.2 2.5,5.3 A4.5,4.5 0 0 1 11.5,5.3 C11.5,8.2 7,13 7,13 Z" fill="none" stroke="var(--orange)" stroke-width="1.1"/><circle cx="7" cy="5.3" r="1.6" fill="none" stroke="var(--orange)" stroke-width="1.1"/></svg>48 Mill Lane, Brookmere</li>
    <li><svg class="contact-icon" viewBox="0 0 14 14"><circle cx="7" cy="7" r="5.8" fill="none" stroke="var(--orange)" stroke-width="1.1"/><ellipse cx="7" cy="7" rx="2.6" ry="5.8" fill="none" stroke="var(--orange)" stroke-width="1.1"/><path d="M1.2,7 H12.8" stroke="var(--orange)" stroke-width="1.1"/></svg>www.brookmereosteopathy.example</li>
    <li><svg class="contact-icon" viewBox="0 0 14 14"><rect x="1.2" y="2.8" width="11.6" height="8.4" rx="1" fill="none" stroke="var(--orange)" stroke-width="1.1"/><path d="M1.5,3.3 L7,7.6 L12.5,3.3" fill="none" stroke="var(--orange)" stroke-width="1.1"/></svg>info@brookmereosteopathy.example</li>
  </ul>
</div>
</body>
</html>
```